Business card for a new cabinet shop company named Veloran Cabinets for high end cabinets

Design a business card, thinking dark rich green with colours to speak of high end luxury ie; cream, gold, black possibly

Mitchell Tarrowby
Director Craftsman
Email: info@veloranjoinery-example.com.au
Instagram : @veloran.cabinets

```html
<!DOCTYPE html>
<html lang="en">
<head>
<meta charset="utf-8">
<title>Veloran Cabinets – Business Card</title>
<link href="https://fonts.googleapis.com/css2?family=Montserrat:wght@400;500;700&display=swap" rel="stylesheet">
<style>
  :root {
    --backdrop: #969696;
    --card: #ffffff;
    --gold: #c9a862;
    --green: #1e3d2f;
    --text: #2b3a32;
  }
  * { box-sizing: border-box; margin: 0; padding: 0; }
  html, body {
    width: 1200px; height: 1108px; overflow: hidden;
    background: var(--backdrop);
    font-family: "Montserrat", sans-serif;
  }
  .card {
    position: absolute; left: 242px;
    width: 715px; height: 409px;
    background: var(--card);
    border-radius: 30px;
  }
  .card--front { top: 119px; }
  .card--back { top: 580px; }

  .brand { position: absolute; display: flex; align-items: center; color: var(--gold); font-weight: 500; }
  .brand__dot { border-radius: 50%; background: var(--green); flex: none; }
  .brand__name { line-height: 1.05; }

  .card--front .brand { left: 78px; top: 138px; gap: 34px; }
  .card--front .brand__dot { width: 118px; height: 118px; }
  .card--front .brand__name { font-size: 64px; }

  .card--back .brand { left: 44px; top: 170px; gap: 18px; }
  .card--back .brand__dot { width: 66px; height: 66px; }
  .card--back .brand__name { font-size: 34px; }

  .divider {
    position: absolute; left: 355px; top: 81px;
    width: 2px; height: 247px; background: var(--gold);
  }
  .contact { position: absolute; left: 380px; top: 80px; color: var(--text); }
  .contact__name { font-size: 29px; font-weight: 700; color: var(--gold); line-height: 1.2; }
  .contact__role { font-size: 18px; margin-top: 4px; color: var(--green); font-weight: 500; }
  .contact__address { font-size: 18px; line-height: 29px; margin-top: 14px; }
  .contact__list { list-style: none; margin-top: 12px; }
  .contact__item { display: flex; align-items: center; gap: 9px; font-size: 15px; height: 28.5px; white-space: nowrap; }
  .contact__icon { width: 15px; height: 15px; flex: none; fill: var(--gold); }
</style>
</head>
<body>
  <section class="card card--front">
    <div class="brand">
      <span class="brand__dot"></span>
      <span class="brand__name">Veloran<br>Cabinets</span>
    </div>
  </section>

  <section class="card card--back">
    <div class="brand">
      <span class="brand__dot"></span>
      <span class="brand__name">Veloran<br>Cabinets</span>
    </div>
    <div class="divider"></div>
    <div class="contact">
      <h1 class="contact__name">Mitchell Tarrowby</h1>
      <p class="contact__role">Director Craftsman</p>
      <p class="contact__address">Your address, City<br>State, Zip 1234</p>
      <ul class="contact__list">
        <li class="contact__item">
          <svg class="contact__icon" viewBox="0 0 16 16"><path d="M1 6c0-2 3-3 7-3s7 1 7 3v1h-3V5.5H4V7H1z"/><rect x="3" y="8" width="10" height="6" rx="1"/></svg>
          123 456 789
        </li>
        <li class="contact__item">
          <svg class="contact__icon" viewBox="0 0 16 16"><path d="M1 3h14v10H1z"/><path d="M2 4l6 5 6-5" fill="none" stroke="#fff" stroke-width="1.2"/></svg>
          info@veloranjoinery-example.com.au
        </li>
        <li class="contact__item">
          <svg class="contact__icon" viewBox="0 0 16 16"><rect x="1" y="1" width="14" height="14" rx="2"/></svg>
          @veloran.cabinets
        </li>
        <li class="contact__item">
          <svg class="contact__icon" viewBox="0 0 16 16"><circle cx="8" cy="8" r="7"/><path d="M1 8h14M8 1c-3 3-3 11 0 14M8 1c3 3 3 11 0 14" fill="none" stroke="#fff" stroke-width="1"/></svg>
          www.veloranjoinery-example.com.au
        </li>
      </ul>
    </div>
  </section>
</body>
</html>
```